tallow-brook.com

We are a small dollar lending company that will revolutionize the industry. We will do this by being completely transparent, fee free, etc and an interest rate that normal people can afford to pay. Over 10X less than our competition. We only allow our members to pay bills " bills paid fast", within 72 hours. Payday loans typically charge from 390%-600% with a terrible payback structure. We charge 36%, period, with a payback structure over 12 months. Our site will be very simple and easy to use but elegant at the same time. We do not want the site to be too busy, less is more and easier. We will have; Home, The Story, Why tallowbrook.com, Are you eligible? Members, Clients. To become a member you have to be referred by a current client of tallowbrook.com. A lot of the busy stuff will be saved for the Members and Clients sections. The feel must be elegant, easy to use and very simple to understand. I am looking for the green, white and black combinations of colors, very similar to my logo that was designed by Fernquillo.

```html
<!DOCTYPE html>
<html lang="en">
<head>
<meta charset="utf-8">
<title>Tallow Brook — Bills Paid Fast</title>
<link href="https://fonts.googleapis.com/css2?family=Roboto:ital,wght@0,300;0,400;0,500;0,700;1,400&display=swap" rel="stylesheet">
<style>
:root{
  --green:#8dc63f;
  --green-dark:#79ad30;
  --black:#0b0b0b;
  --footer:#161616;
  --footer-deep:#0e0e0e;
  --grey-band:#e6e6e6;
  --text:#222;
  --muted:#555;
  --white:#fff;
}
*{box-sizing:border-box;margin:0;padding:0}
html,body{width:1162px;height:1200px;overflow:hidden}
body{font-family:"Roboto",Arial,sans-serif;color:var(--text);background:var(--white);position:relative}
.abs{position:absolute}

.top-band{left:0;top:0;width:1162px;height:100px;background:var(--green);border-top:3px solid var(--black)}
.brand{left:194px;top:16px;display:flex;align-items:center;gap:8px;color:var(--white);font-size:20px;font-weight:300;letter-spacing:.5px}
.brand-dot{width:30px;height:30px;border-radius:50%;border:5px solid var(--white)}
.member-login{left:898px;top:30px;width:70px;height:19px;background:#f4f4f4;border:1px solid #bbb;font-size:8.5px;color:#111;display:flex;align-items:center;justify-content:center}

.main-nav{left:194px;top:75px;width:774px;height:47px;background:var(--black);z-index:3}
.main-nav a{position:absolute;top:19px;color:var(--white);font-size:10px;text-decoration:none}
.main-nav a.active::after{content:"";position:absolute;left:-8px;right:-8px;top:23px;height:3px;background:var(--green)}
.nav-icons{position:absolute;left:621px;top:13px;display:flex;gap:4px}
.nav-icons span{width:19px;height:19px;background:#3a3a3a;display:flex;align-items:center;justify-content:center}
.nav-icons span.search{background:#444}

.hero{left:0;top:100px;width:1162px;height:431px;background:linear-gradient(100deg,#c9c2b2 0%,#e4e1da 30%,#eeece8 55%,#d8d2c8 80%,#b9a98f 100%)}
.hero-caption{left:194px;top:276px;width:206px;height:57px;background:var(--green);color:var(--white);font-size:23px;padding:14px 0 0 19px;box-shadow:0 1px 3px rgba(0,0,0,.3)}
.hero-arrow{top:281px;width:48px;height:54px;background:rgba(40,40,40,.85);display:flex;align-items:center;justify-content:center}
.hero-arrow.left{left:0}
.hero-arrow.right{left:1118px;border-radius:3px 0 0 3px}
.hero-dots{left:555px;top:511px;display:flex;gap:6px}
.hero-dots span{width:10px;height:10px;border-radius:50%;background:var(--white);border:1px solid #999}
.hero-dots span.on{background:var(--green)}

.welcome{left:0;top:531px;width:1162px;height:172px;background:var(--grey-band);text-align:center}
.welcome h1{margin-top:23px;font-size:24px;font-weight:400;color:#111}
.welcome h1 em{font-style:normal;color:var(--green)}
.welcome p{width:780px;margin:9px auto 0;font-size:10px;line-height:23.2px;color:var(--muted)}

.section-title{font-size:15px;font-weight:400;color:#111}
.pager{font-size:7px;color:#111;letter-spacing:2px}
.member-box{left:193px;top:772px;width:217px;height:165px;background:var(--green);border:1px solid #d6d6d6;color:var(--white);padding:0 11px}
.member-box p{position:absolute;left:11px;top:81px;width:196px;font-size:9.6px;line-height:18.6px}
.member-box .more{position:absolute;right:11px;top:141px;font-size:9.6px;font-style:italic;color:#222}

.news-item{left:427px;width:300px;height:70px}
.news-thumb{position:absolute;left:0;top:0;width:73px;height:69px;border:1px solid #ddd}
.news-item h3{position:absolute;left:85px;top:7px;font-size:10.5px;font-weight:500;color:#444;letter-spacing:.3px}
.news-item p{position:absolute;left:85px;top:26px;width:190px;font-size:9.2px;line-height:11px;color:#555}
.news-item a{position:absolute;left:85px;top:54px;font-size:9.5px;color:var(--green);text-decoration:none;font-weight:500}

.client-photo{left:816px;top:774px;width:67px;height:67px;border-radius:50%;background:radial-gradient(circle at 50% 45%,#c9a085,#7a5a46);border:2px solid #eee}
.client-quote{left:748px;top:845px;width:200px;text-align:center;font-size:11.5px;line-height:18.6px;color:#555;font-weight:300}
.client-name{left:880px;top:925px;font-size:11.5px;color:#111}

.footer{left:0;top:977px;width:1162px;height:186px;background:var(--footer)}
.footer h4{position:absolute;top:28px;font-size:11.5px;font-weight:400;color:var(--green)}
.footer ul{position:absolute;list-style:none;font-size:9.6px;line-height:18.6px;color:var(--white)}
.footer .green{color:var(--green)}
.follow{position:absolute;left:827px;top:53px;display:flex;gap:12px}
.follow span{font-size:9.6px;color:var(--white);display:flex;align-items:center;gap:4px}
.follow span i{width:8px;height:8px;background:var(--green);display:block}
.newsletter{position:absolute;left:827px;top:127px;display:flex}
.newsletter .field{width:90px;height:26px;background:var(--white);font-size:8.5px;font-style:italic;color:#222;padding:8px 0 0 8px}
.newsletter .submit{width:51px;height:26px;background:var(--green);color:var(--white);font-size:9.6px;font-style:italic;display:flex;align-items:center;justify-content:center}
.copyright{left:0;top:1163px;width:1162px;height:37px;background:var(--footer-deep);color:var(--green);font-size:9.2px;text-align:center;padding-top:13px}
</style>
</head>
<body>

<header class="abs top-band"></header>
<div class="abs brand"><span class="brand-dot"></span>Tallow Brook</div>
<div class="abs member-login">Member Login</div>

<nav class="abs main-nav">
  <a href="#" class="active" style="left:27px">Home</a>
  <a href="#" style="left:114px">The Story</a>
  <a href="#" style="left:216px">Why tallowbrook.com</a>
  <a href="#" style="left:359px">Are you eligible? Members</a>
  <a href="#" style="left:508px">Clients</a>
  <div class="nav-icons">
    <span class="search"><svg width="10" height="10" viewBox="0 0 10 10"><circle cx="4" cy="4" r="3" fill="none" stroke="#fff" stroke-width="1.4"/><line x1="6.2" y1="6.2" x2="9" y2="9" stroke="#fff" stroke-width="1.6"/></svg></span>
    <span title="Chirpa"></span><span title="Facet"></span><span title="Dotball"></span><span title="Linkwork"></span><span title="Feedline"></span>
  </div>
</nav>

<section class="abs hero" role="img" aria-label="Photo of coins resting on a restaurant receipt beside a white coffee cup and saucer"></section>
<div class="abs hero-caption">Bills Paid Fast</div>
<div class="abs hero-arrow left"><svg width="16" height="22" viewBox="0 0 16 22"><polyline points="12,3 4,11 12,19" fill="none" stroke="#fff" stroke-width="4"/></svg></div>
<div class="abs hero-arrow right"><svg width="16" height="22" viewBox="0 0 16 22"><polyline points="4,3 12,11 4,19" fill="none" stroke="#fff" stroke-width="4"/></svg></div>
<div class="abs hero-dots"><span class="on"></span><span></span><span></span></div>

<section class="abs welcome">
  <h1>Welcome To <em>Tallow Brook</em></h1>
  <p>Lorem ipsum dolor sit amet, consectetur adipiscing elit. Consectetur adipisicing elit, sed do eiusmod tempor incididunt ut labore et dolore magna aliqua. Ut enim ad minim veniam, quis nostrud.Lorem ipsum dolor sit amet, consectetur adipiscing elit. Consectetur adipisicing elit, sed do eiusmod tempor incididunt ut labore et dolore magna aliqua. Ut enim ad minim veniam, quis nostrud.Lorem ipsum dolor sit amet, consectetur adipiscing elit. Consectetur adipisicing elit, sed do eiusmod tempor incididunt ut labore et dolore magna aliqua. Ut enim ad minim veniam, quis nostrud.</p>
</section>

<h2 class="abs section-title" style="left:193px;top:744px">Become a Member</h2>
<div class="abs pager" style="left:403px;top:748px">◂▸</div>
<div class="abs member-box">
  <svg class="abs" style="left:63px;top:26px" width="88" height="46" viewBox="0 0 88 46">
    <g fill="#fff">
      <circle cx="44" cy="12" r="11"/><path d="M26 46 Q26 26 44 25 Q62 26 62 46Z"/>
      <circle cx="17" cy="17" r="8.5"/><path d="M2 46 Q3 30 17 29 Q27 30 29 38 L27 46Z"/>
      <circle cx="71" cy="17" r="8.5"/><path d="M86 46 Q85 30 71 29 Q61 30 59 38 L61 46Z"/>
    </g>
  </svg>
  <p>The management consulting firm the world's business leaders come to when they want The management consulting firm the world's busi-</p>
  <span class="more">-Read More +</span>
</div>

<h2 class="abs section-title" style="left:426px;top:744px">News</h2>
<div class="abs" style="left:660px;top:748px;font-size:9.6px;color:#111">View more +</div>
<article class="abs news-item" style="top:772px">
  <div class="news-thumb" role="img" aria-label="Spa still life with a white flower and a small oil bottle" style="background:linear-gradient(135deg,#8a6a4a,#e8e0d0 55%,#c89a3a)"></div>
  <h3>SUSPENDISSE MATTIS TELI</h3>
  <p>Suspendisse mattis tellus vel augue mollis ultrices suspends</p>
  <a href="#">Read More +</a>
</article>
<article class="abs news-item" style="top:855px">
  <div class="news-thumb" role="img" aria-label="Close view of a relaxing massage" style="background:linear-gradient(135deg,#f3c9a0,#e89a58 60%,#d9864a)"></div>
  <h3>SUSPENDISSE MATTIS TELI</h3>
  <p>Suspendisse mattis tellus vel augue mollis ultrices suspends</p>
  <a href="#">Read More +</a>
</article>

<h2 class="abs section-title" style="left:748px;top:744px">Clients</h2>
<div class="abs pager" style="left:954px;top:744px">◂▸</div>
<div class="abs client-photo" role="img" aria-label="Portrait of a smiling client"></div>
<p class="abs client-quote">Donec sed odio dui. Nullam id dolor id nibh ultricies vehicula ut id elit. Sollicitu-din Lorem Egestas Dapibus.</p>
<div class="abs" style="left:868px;top:908px;font-size:12px;color:#777">"</div>
<div class="abs client-name">Mr.Oren, Manager</div>

<footer class="abs footer">
  <h4 style="left:194px">Brands We Stock</h4>
  <ul style="left:194px;top:48px"><li>Home</li><li>The Story</li><li>Why tallowbrook.com</li><li>Are you eligible? Members,</li><li>Clients</li></ul>
  <h4 style="left:381px">Contact Us</h4>
  <ul style="left:381px;top:48px"><li>417 Linden Row</li><li>Marlow, OR 97120</li><li>Phone: 555-014-2286</li><li>E-mail: hello@tallowbrook.com</li></ul>
  <h4 style="left:559px">Latest Posts</h4>
  <ul style="left:559px;top:45px;width:180px"><li>Thoroughly European quarter</li><li>He had nothing better to do than, taking chance for his guide, to wander aimlessly</li><li class="green">October 25</li></ul>
  <h4 style="left:827px">Follow us</h4>
  <div class="follow"><span><i></i>Facet</span><span><i></i>Chirpa</span><span><i></i>Plusr</span><span><i></i>Feedline</span></div>
  <h4 style="left:827px;top:106px">Newsletters</h4>
  <div class="newsletter"><div class="field">Email Address</div><div class="submit">Submit</div></div>
</footer>
<div class="abs copyright">COPYRIGHT © Tallow Brook. ALL RIGHTS RESERVED.</div>

</body>
</html>
```